A start-up named "Corvane Therapeutics" - needs a new PowerPoint design

We need a new PowerPoint Design for an early-stage start-up named "Corvane Therapeutics" seeking to disrupt the current approach towards drug discovery within aging disorders.

We would like to build on Corvane's legacy, the founder of the modern science of genetics, by employing a multidisciplinary approach, experimenting, and providing elderly patients the attention they deserve.

We have selected the suffix "therapeutics" intentionally as it stands for (a medicine) the treatment of disease; the science of healing. Alzheimer’s treatment is a huge, urgent, unmet need:
- Shift from a disease-management system to a preventive medicine system
- Focus on increasing the health span, not only the life span

Target Market(s)

Pharma/ Biotech Executives Medical Institutions Healthcare professionals (MDs, nurses, payors, pharmacists, etc.) Patients

Industry/Entity Type

Healthcare

Other font styles liked:
• Celias

Colors
0054AA
0677BA
7BADD7
CADEEF
E8F1F8
E54698
E96AAD
F1A4CE
F9D9EA
FCEFF6
A7469A
B969AE
D3A5CF
EDDBEB
F8F0F9
6B429C
8869AF
B7A5CE
E3DAEB
F3F0F8

Requirements
Must have
• - differentiate from other companies named after Corvane - differentiate from other Pharma/ Biotech companies
Nice to have
• simplicity/ minimalist logo vivid colors gradient 3D Life-Sciences inspired Simple geometry Balance
Should not have
• mascot/ emblem watermark logo animated ink style nature-inspired inventive typography artistic chaos

```html
<!DOCTYPE html>
<html lang="en">
<head>
<meta charset="utf-8">
<title>Corvane Therapeutics – Presentation Template</title>
<link rel="stylesheet" href="https://fonts.googleapis.com/css2?family=Poppins:wght@400;500;600;700&display=swap">
<style>
  :root{
    --blue:#1aa3e4;
    --blue-dark:#0677ba;
    --purple:#6e2a8c;
    --purple-soft:#a7469a;
    --ink:#2f2f3a;
    --text:#5b5b66;
    --page:#f3f3f6;
    --white:#ffffff;
  }
  *{box-sizing:border-box;margin:0;padding:0}
  html,body{width:1200px;height:3368px;overflow:hidden}
  body{background:var(--page);font-family:"Poppins",sans-serif;color:var(--text);position:relative}

  .slide{position:absolute;left:40px;width:1120px;height:630px;background:var(--white);overflow:hidden;box-shadow:0 4px 18px rgba(40,30,70,.12)}
  .slide--cover{top:40px}
  .slide--list{top:700px}
  .slide--story{top:1360px}
  .slide--stats{top:2020px}
  .slide--thanks{top:2680px}

  .brand{position:absolute;display:flex;align-items:center;gap:10px;color:var(--blue-dark);font-weight:600;font-size:19px;line-height:1.05}
  .brand__mark{width:26px;height:26px;background:var(--purple)}
  .brand__name small{display:block;font-size:13px;font-weight:600}

  .title{position:absolute;font-weight:700;font-size:46px;line-height:1.12;color:var(--blue)}
  .title span{display:block;color:var(--ink)}

  .copy{font-size:13px;line-height:1.6;color:var(--text)}
  .subhead{font-size:15px;font-weight:600;color:var(--purple);margin:14px 0 8px}

  .bullets{list-style:none}
  .bullets li{position:relative;padding-left:20px;font-size:12.5px;line-height:1.4;margin-bottom:7px}
  .bullets li::before{content:"";position:absolute;left:0;top:5px;width:8px;height:8px;border-radius:50%;background:var(--purple)}

  .footer{position:absolute;left:48px;bottom:18px;font-size:12px;color:var(--purple);font-weight:500}
  .footer b{font-weight:400;margin:0 10px;color:var(--blue)}

  .photo{position:absolute}
  .abs{position:absolute}

  .rings{position:absolute;left:48px;top:460px;display:flex;gap:34px}
  .ring{position:relative;width:90px;height:90px}
  .ring span{position:absolute;inset:0;display:flex;align-items:center;justify-content:center;font-weight:600;font-size:17px;color:var(--ink)}

  .contacts{position:absolute;left:650px;top:370px;display:grid;grid-template-columns:210px 210px;row-gap:26px;font-size:12.5px;line-height:1.45}
  .contact{display:flex;gap:12px;align-items:flex-start}
  .contact strong{display:block;color:var(--purple);font-weight:600}
  .contact--wide{grid-column:1/3}
</style>
</head>
<body>

<!-- Slide 1: cover -->
<section class="slide slide--cover">
  <div class="brand" style="left:48px;top:40px"><div class="brand__mark"></div><div class="brand__name">Corvane<small>Therapeutics</small></div></div>
  <svg class="photo" style="left:0;top:0" width="1120" height="630" role="img" aria-label="Photo of a scientist in protective gear working at a laboratory microscope">
    <defs><linearGradient id="labGrad" x1="0" y1="0" x2="1" y2="1"><stop offset="0" stop-color="#cfe3f3"/><stop offset=".55" stop-color="#6f9ccc"/><stop offset="1" stop-color="#e9eef5"/></linearGradient></defs>
    <polygon points="520,0 1120,0 1120,630 640,630" fill="url(#labGrad)"/>
  </svg>
  <svg class="abs" style="left:0;top:0" width="1120" height="630" aria-hidden="true">
    <polygon points="470,0 540,0 640,520 600,520" fill="var(--purple)"/>
    <polygon points="540,0 720,0 560,110" fill="var(--blue)"/>
    <rect x="0" y="616" width="560" height="14" fill="var(--purple)"/>
    <rect x="560" y="616" width="560" height="14" fill="var(--blue)"/>
  </svg>
  <h1 class="title" style="left:48px;top:330px">Neque porro<br>quisquam est qui<span>dolorem ipsum</span></h1>
  <div class="footer" style="bottom:28px">www.CorvaneTherapeutics.com<b>|</b>+1 (555) 014 7890</div>
</section>

<!-- Slide 2: text and bullet list -->
<section class="slide slide--list">
  <div class="brand" style="left:48px;top:30px"><div class="brand__mark"></div><div class="brand__name">Corvane<small>Therapeutics</small></div></div>
  <div class="abs" style="right:0;top:0;width:160px;height:630px;background:var(--purple)"></div>
  <div class="abs" style="left:920px;top:330px;width:40px;height:300px;background:var(--blue)"></div>
  <svg class="photo" style="left:560px;top:120px" width="420" height="310" role="img" aria-label="Illustration of a chromosome in soft blue light">
    <defs><radialGradient id="chromGrad" cx=".5" cy=".5" r=".7"><stop offset="0" stop-color="#f3d6ee"/><stop offset=".5" stop-color="#9cc8ea"/><stop offset="1" stop-color="#4a8fcf"/></radialGradient></defs>
    <rect width="420" height="310" fill="url(#chromGrad)"/>
  </svg>
  <h2 class="title" style="left:48px;top:100px;font-size:40px">Neque porro<span>quisquam est qui</span></h2>
  <div class="abs" style="left:48px;top:210px;width:440px">
    <p class="copy">Sed ut perspiciatis unde omnis iste natus error sit voluptatem accusantium doloremque laudantium totam rem aperiam eaque ipsa quae ab illo inventore veritatis et quasi architecto beatae vitae dicta sunt explicabo.</p>
    <p class="subhead">Nemo enim ipsam voluptatem quia voluptas</p>
    <ul class="bullets">
      <li>Sed ut perspiciatis unde omnis iste natus error sit voluptatem</li>
      <li>Doloremque laudantium totam rem aperiam eaque ipsa quae ab illo inventore veritatis</li>
      <li>Beatae vitae dicta sunt explicabo</li>
      <li>Sed ut perspiciatis unde omnis iste natus error sit voluptatem</li>
      <li>Doloremque laudantium totam rem aperiam eaque ipsa quae ab illo inventore veritatis</li>
      <li>Beatae vitae dicta sunt explicabo</li>
    </ul>
  </div>
  <div class="footer">www.CorvaneTherapeutics.com<b>|</b>+1 (555) 014 7890</div>
</section>

<!-- Slide 3: image with long text -->
<section class="slide slide--story">
  <svg class="photo" style="left:0;top:0" width="560" height="570" role="img" aria-label="Illustration of a glowing red DNA double helix">
    <defs><linearGradient id="dnaGrad" x1="0" y1="0" x2="1" y2="1"><stop offset="0" stop-color="#3a0f2a"/><stop offset=".5" stop-color="#c8283f"/><stop offset="1" stop-color="#5a1030"/></linearGradient></defs>
    <polygon points="0,0 500,0 400,570 0,570" fill="url(#dnaGrad)"/>
  </svg>
  <svg class="abs" style="left:0;top:0" width="620" height="630" aria-hidden="true">
    <polygon points="500,0 560,0 460,570 400,570" fill="var(--purple)"/>
    <polygon points="0,470 340,430 300,570 0,570" fill="var(--blue)"/>
    <rect x="0" y="570" width="260" height="10" fill="var(--purple)"/>
  </svg>
  <div class="brand" style="right:48px;top:30px"><div class="brand__mark"></div><div class="brand__name">Corvane<small>Therapeutics</small></div></div>
  <h2 class="title" style="right:48px;top:110px;text-align:right;font-size:40px">Quisquam est qui<span>dolorem ipsum</span></h2>
  <div class="abs copy" style="left:590px;top:230px;width:482px;text-align:justify">
    <p>Sed ut perspiciatis unde omnis iste natus error sit voluptatem accusantium doloremque laudantium totam rem aperiam eaque ipsa quae ab illo inventore veritatis et quasi architecto beatae vitae dicta sunt explicabo.</p>
    <p style="margin-top:12px">Nemo enim ipsam voluptatem quia voluptas sit aspernatur aut odit aut fugit sed quia consequuntur magni dolores eos qui ratione voluptatem sequi nesciunt neque porro quisquam est qui dolorem ipsum quia dolor sit amet consectetur adipisci velit.</p>
    <p style="margin-top:12px;text-align:right">Ut enim ad minima veniam quis nostrum exercitationem ullam corporis suscipit laboriosam nisi ut aliquid ex ea commodi consequatur quis autem vel eum iure reprehenderit.</p>
  </div>
  <div class="footer">www.CorvaneTherapeutics.com<b>|</b>+1 (555) 014 7890</div>
</section>

<!-- Slide 4: statistics -->
<section class="slide slide--stats">
  <div class="brand" style="left:48px;top:30px"><div class="brand__mark"></div><div class="brand__name">Corvane<small>Therapeutics</small></div></div>
  <div class="abs" style="right:0;top:0;width:160px;height:570px;background:var(--purple)"></div>
  <div class="abs" style="left:880px;top:440px;width:80px;height:190px;background:var(--blue)"></div>
  <svg class="photo" style="left:540px;top:100px" width="400" height="440" role="img" aria-label="Photo of assorted colourful pills on a dark blue surface">
    <defs><radialGradient id="pillGrad" cx=".5" cy=".45" r=".6"><stop offset="0" stop-color="#3b4f7a"/><stop offset="1" stop-color="#15204a"/></radialGradient></defs>
    <rect width="400" height="440" fill="url(#pillGrad)"/>
  </svg>
  <h2 class="title" style="left:48px;top:100px;font-size:40px">Neque porro<span>quisquam est qui</span></h2>
  <div class="abs" style="left:48px;top:210px;width:440px">
    <p class="copy">Sed ut perspiciatis unde omnis iste natus error sit voluptatem accusantium doloremque laudantium totam rem aperiam eaque ipsa quae ab illo inventore veritatis et quasi architecto beatae vitae dicta sunt explicabo.</p>
    <p class="subhead">Nemo enim ipsam voluptatem quia voluptas</p>
    <p class="copy">Ut enim ad minima veniam quis nostrum exercitationem ullam corporis suscipit laboriosam.</p>
  </div>
  <div class="rings">
    <div class="ring"><svg width="90" height="90"><circle cx="45" cy="45" r="39" fill="none" stroke="#ece4f1" stroke-width="8"/><circle cx="45" cy="45" r="39" fill="none" stroke="var(--purple)" stroke-width="8" stroke-dasharray="159.3 245" transform="rotate(-90 45 45)"/></svg><span>65%</span></div>
    <div class="ring"><svg width="90" height="90"><circle cx="45" cy="45" r="39" fill="none" stroke="#e3f1fa" stroke-width="8"/><circle cx="45" cy="45" r="39" fill="none" stroke="var(--blue)" stroke-width="8" stroke-dasharray="208.3 245" transform="rotate(-90 45 45)"/></svg><span>85%</span></div>
    <div class="ring"><svg width="90" height="90"><circle cx="45" cy="45" r="39" fill="none" stroke="#ece4f1" stroke-width="8"/><circle cx="45" cy="45" r="39" fill="none" stroke="var(--purple)" stroke-width="8" stroke-dasharray="232.8 245" transform="rotate(-90 45 45)"/></svg><span>95%</span></div>
  </div>
  <div class="footer">www.CorvaneTherapeutics.com<b>|</b>+1 (555) 014 7890</div>
</section>

<!-- Slide 5: thank you and contacts -->
<section class="slide slide--thanks">
  <div class="abs" style="left:0;top:420px;width:120px;height:210px;background:var(--purple)"></div>
  <div class="abs" style="left:120px;top:520px;width:440px;height:20px;background:var(--blue)"></div>
  <svg class="photo" style="left:40px;top:70px" width="520" height="450" role="img" aria-label="Photo of a gloved hand using a pipette over a laboratory sample tray">
    <defs><linearGradient id="sampleGrad" x1="0" y1="0" x2="1" y2="1"><stop offset="0" stop-color="#1d2f55"/><stop offset=".5" stop-color="#6d9cc9"/><stop offset="1" stop-color="#dfeaf4"/></linearGradient></defs>
    <rect width="520" height="450" fill="url(#sampleGrad)"/>
  </svg>
  <div class="brand" style="right:48px;top:30px"><div class="brand__mark"></div><div class="brand__name">Corvane<small>Therapeutics</small></div></div>
  <h2 class="title" style="left:650px;top:150px;font-size:42px">Thank You!<span>quisquam est qui</span></h2>
  <p class="abs copy" style="left:650px;top:280px;width:420px">Sed ut perspiciatis unde omnis iste natus error sit voluptatem accusantium doloremque laudantium totam rem aperiam.</p>
  <div class="contacts">
    <div class="contact">
      <svg width="32" height="32" viewBox="0 0 32 32" aria-hidden="true"><circle cx="16" cy="16" r="15" fill="none" stroke="var(--purple)" stroke-width="2"/><path d="M11 9l3 0 1.5 4-2 1.5c1 2 2.5 3.5 4.5 4.5l1.5-2 4 1.5v3c0 1-1 1.5-2 1.5C15 23 9 17 9 11c0-1 .5-2 2-2z" fill="var(--purple)"/></svg>
      <div><strong>Phone:</strong>+1 (555) 014 7890</div>
    </div>
    <div class="contact">
      <svg width="32" height="32" viewBox="0 0 32 32" aria-hidden="true"><circle cx="16" cy="16" r="15" fill="none" stroke="var(--purple)" stroke-width="2"/><rect x="9" y="11" width="14" height="10" rx="1" fill="none" stroke="var(--purple)" stroke-width="2"/><path d="M9 12l7 5 7-5" fill="none" stroke="var(--purple)" stroke-width="2"/></svg>
      <div><strong>Email:</strong>hello@corvanetx.com</div>
    </div>
    <div class="contact contact--wide">
      <svg width="32" height="32" viewBox="0 0 32 32" aria-hidden="true"><circle cx="16" cy="16" r="15" fill="none" stroke="var(--purple)" stroke-width="2"/><path d="M16 8a5 5 0 0 0-5 5c0 4 5 10 5 10s5-6 5-10a5 5 0 0 0-5-5z" fill="var(--purple)"/><circle cx="16" cy="13" r="2" fill="#fff"/></svg>
      <div>2400 Harbor Crest Drive, Suite 810<br>Weston, FL 33326</div>
    </div>
  </div>
</section>

</body>
</html>
```